New Company Business Card design

Looking for a corporate looking business card utilising my new logo design - the logo i would like embossed as one option and flat as another - simplistic but stylish - less is more - we are an import export business launching into the market - i would like a couple of options as main background - Grey or Black

```html
<!DOCTYPE html>
<html lang="en">
<head>
<meta charset="utf-8">
<title>Northgate Trade Partners – Business Card</title>
<link rel="stylesheet" href="https://fonts.googleapis.com/css2?family=Arimo:wght@400;700&display=swap">
<style>
  :root {
    --backdrop: #ece8e2;
    --card-white: #fbfbfa;
    --card-dark: #2a2a2c;
    --brand-blue: #1673c6;
    --brand-grey: #7d7f82;
    --text-light: #d9d9d9;
    --text-muted: #8e8f92;
  }
  * { box-sizing: border-box; margin: 0; padding: 0; }
  html, body {
    width: 1200px; height: 848px; overflow: hidden;
    background: var(--backdrop);
    font-family: "Arimo", Arial, sans-serif;
  }
  .canvas { position: relative; width: 1200px; height: 848px; }
  .card {
    position: absolute; left: 280px; width: 640px; height: 366px;
    box-shadow: 0 6px 18px rgba(0,0,0,0.18);
    overflow: hidden;
  }
  .card--front { top: 40px; background: var(--card-white); }
  .card--back { top: 442px; background: var(--card-dark); }

  /* Front: name lockup */
  .brand {
    position: absolute; inset: 0;
    display: flex; flex-direction: column; align-items: center; justify-content: center;
  }
  .brand__row { display: flex; align-items: center; gap: 14px; }
  .brand__dot { width: 26px; height: 26px; border-radius: 50%; background: var(--brand-blue); }
  .brand__name {
    color: var(--brand-blue); font-weight: 700; font-size: 30px;
    letter-spacing: 1.5px; text-transform: uppercase; white-space: nowrap;
  }
  .brand__rule { width: 380px; height: 2px; background: var(--brand-grey); margin: 12px 0 10px; }
  .brand__tagline {
    color: var(--brand-grey); font-weight: 700; font-size: 13px;
    letter-spacing: 2.5px; text-transform: uppercase; white-space: nowrap;
  }

  /* Back: contact details */
  .accent { position: absolute; right: 0; top: 0; width: 340px; height: 366px; }
  .contact { position: absolute; left: 44px; top: 118px; color: var(--text-light); }
  .contact__name { color: var(--brand-blue); font-weight: 700; font-size: 21px; letter-spacing: 0.5px; }
  .contact__title { color: var(--text-muted); font-size: 13px; margin-top: 3px; letter-spacing: 0.5px; }
  .contact__address { font-size: 14px; line-height: 19px; margin-top: 12px; }
  .contact__list { list-style: none; margin-top: 14px; }
  .contact__item { display: flex; align-items: center; gap: 10px; font-size: 14px; line-height: 20px; white-space: nowrap; }
  .contact__icon { width: 13px; height: 13px; fill: var(--brand-blue); flex: none; }
</style>
</head>
<body>
<main class="canvas">

  <section class="card card--front" aria-label="Card front">
    <div class="brand">
      <div class="brand__row">
        <span class="brand__dot"></span>
        <span class="brand__name">Northgate Trade Partners</span>
      </div>
      <div class="brand__rule"></div>
      <div class="brand__tagline">Trusted trade from port to doorstep</div>
    </div>
  </section>

  <section class="card card--back" aria-label="Card back">
    <svg class="accent" viewBox="0 0 340 366" role="img" aria-label="Blue curved corner panel">
      <path d="M340 0 L150 0 C250 30 330 130 300 366 L340 366 Z" fill="var(--brand-blue)"/>
    </svg>

    <div class="contact">
      <div class="contact__name">DANIEL REYES</div>
      <div class="contact__title">CEO/FOUNDER</div>
      <div class="contact__address">2140 Harbor View Road<br>Seaport, Oregon 97210</div>
      <ul class="contact__list">
        <li class="contact__item">
          <svg class="contact__icon" viewBox="0 0 16 16"><path d="M3 1h3l1.5 4-2 1.3a9 9 0 0 0 4.2 4.2L11 8.5l4 1.5v3a2 2 0 0 1-2 2A13 13 0 0 1 1 3a2 2 0 0 1 2-2z"/></svg>
          503 214 7780
        </li>
        <li class="contact__item">
          <svg class="contact__icon" viewBox="0 0 16 16"><path d="M4 0h8a1 1 0 0 1 1 1v14a1 1 0 0 1-1 1H4a1 1 0 0 1-1-1V1a1 1 0 0 1 1-1zm1 2v10h6V2zm3 11a1 1 0 1 0 0 2 1 1 0 0 0 0-2z"/></svg>
          503 618 2245
        </li>
        <li class="contact__item">
          <svg class="contact__icon" viewBox="0 0 16 16"><path d="M4 0h7v4H4zM1 5h14v7h-3v4H4v-4H1zm5 6v3h4v-3z"/></svg>
          503 907 3316
        </li>
        <li class="contact__item">
          <svg class="contact__icon" viewBox="0 0 16 16"><path d="M0 3h16v1.5L8 9 0 4.5zm0 3.2 8 4.5 8-4.5V13H0z"/></svg>
          daniel@northgatetrade.com
        </li>
        <li class="contact__item">
          <svg class="contact__icon" viewBox="0 0 16 16"><path d="M8 0a8 8 0 1 0 0 16A8 8 0 0 0 8 0zm0 1.5c.9 0 2 1.8 2.3 5H5.7C6 3.3 7.1 1.5 8 1.5zM1.6 7.5h2.6a16 16 0 0 1 .4-4.3 6.5 6.5 0 0 0-3 4.3zm0 1h2.6a16 16 0 0 0 .4 4.3 6.5 6.5 0 0 1-3-4.3zm4.1 0h4.6c-.3 3.2-1.4 5-2.3 5s-2-1.8-2.3-5zm6.1 0h2.6a6.5 6.5 0 0 1-3 4.3 16 16 0 0 0 .4-4.3zm0-1a16 16 0 0 0-.4-4.3 6.5 6.5 0 0 1 3 4.3z"/></svg>
          www.northgatetrade.com
        </li>
      </ul>
    </div>
  </section>

</main>
</body>
</html>
```